Design einer Kundenkarte für Handelsunternehmen
Zielgruppe
Wir sind ein Handelsunternehmen für Afro Kosmetik und für Kosmetik für Menschen mit lockigem Haar. Wir wollen eine Kundenkarte mit verschiedenen Levels herausbringen.
Aufgabenstellung
Die Kundenkarte hat verschiedene Levels für jedes Level soll ein eigenes Kartendesign entwickelt werden.
Level 1 = Lady/Sir = Ist eine kostenlose Karte, die jeder bekommen kann
Level 2 = Contessa/Conte = ist eine Karte, die an einen bestimmten Umsatz gebunden ist
Level 3 = Princes/Prince = ist eine Karte, die an einen Höheren Umsatz gebunden ist.
Level 4 = Queen/King = ist eine Karte, die an einen noch höheren Umsatz gebunden ist
Level 5 = Profesional = Ist eine Karte, die nur an gewerbliche Kunden herausgegeben wird.
Die Kundenkarte wird auf eine NFC Karte gedruckt,
Folgende Elemente soll die Kundenkarte beinhalten:
Vorderseite der Karte:
Vorname und Nachname des Kunden
Kundennummer
Kartennummer
Kundennummer als QR Code
Gültigkeit bis MM/JJJJ
Foto des Kunden
Rückseite der Karte
Unterschriftsfeld
Sicherheitscode soll auf der Rückseite

```html
<!DOCTYPE html>
<html lang="de">
<head>
<meta charset="utf-8">
<title>Kundenkarte Level 2</title>
<link rel="stylesheet" href="https://fonts.googleapis.com/css2?family=Lexend:wght@300;400&family=Open+Sans:wght@400&family=Caveat:wght@400&display=swap">
<style>
  :root {
    --paper: #ffffff;
    --ink: #111111;
    --card-dark: #000000;
    --card-light: #dadbdd;
    --silhouette-light: #58585a;
    --silhouette-dark: #333333;
    --gold-text: #d9ccab;
    --chip-orange: #f5b335;
    --photo-tone: #6b4a3a;
  }
  * { margin: 0; padding: 0; box-sizing: border-box; }
  html, body { width: 849px; height: 1200px; overflow: hidden; background: var(--paper); }
  .sheet { position: relative; width: 849px; height: 1200px; font-family: "Open Sans", sans-serif; color: var(--ink); }
  .sheet-label { position: absolute; left: 50px; top: 36px; font-size: 16px; line-height: 21px; }

  .card { position: absolute; border-radius: 20px; overflow: hidden; }
  .card--front { left: 377px; top: 131px; width: 337px; height: 219px; background: var(--card-dark); }
  .card--back { left: 379px; top: 394px; width: 338px; height: 218px; background: var(--card-light); }

  .front-artwork {
    position: absolute; left: 60px; top: 8px; width: 260px; height: 211px;
    border-radius: 105px 105px 0 60px;
    background: linear-gradient(90deg, var(--silhouette-light) 0%, var(--silhouette-light) 55%, var(--silhouette-dark) 80%, var(--card-dark) 100%);
  }
  .brand-name {
    position: absolute; font-family: "Lexend", sans-serif; font-weight: 300;
    font-size: 34px; line-height: 42px; letter-spacing: 0.2px; white-space: nowrap;
  }
  .card--front .brand-name { left: 17px; top: 39px; color: #ffffff; }
  .card--back .brand-name { left: 19px; top: 148px; color: var(--ink); }
  .card-tier {
    position: absolute; left: 22px; top: 180px; font-family: "Caveat", cursive;
    font-size: 22px; line-height: 28px; color: var(--gold-text); white-space: nowrap;
  }

  .holder-name {
    position: absolute; left: 22px; top: 16px; font-family: "Lexend", sans-serif; font-weight: 400;
    font-size: 15.5px; line-height: 22px;
  }
  .holder-data { position: absolute; left: 22px; font-size: 10.5px; line-height: 14px; white-space: nowrap; }
  .holder-data--number { top: 72px; }
  .holder-data--code { top: 89px; }
  .holder-data--security { top: 110px; left: 20px; font-size: 9.5px; }
  .holder-photo { position: absolute; left: 232px; top: 18px; width: 91px; height: 112px; background: var(--photo-tone); }
  .valid-until { position: absolute; left: 240px; top: 135px; font-size: 9.5px; line-height: 14px; white-space: nowrap; }
  .nfc-field {
    position: absolute; left: 234px; top: 165px; width: 104px; height: 53px;
    background: var(--chip-orange); border-radius: 20px 0 20px 20px;
  }
</style>
</head>
<body>
<main class="sheet">
  <p class="sheet-label">DL_Kundenkarte_Version 4<br>L2</p>

  <section class="card card--front" aria-label="Kartenvorderseite">
    <div class="front-artwork" role="img" aria-label="Silhouetten von drei Köpfen mit lockigem Haar und Zöpfen in Grautönen"></div>
    <div class="brand-name">Amara-Lumi</div>
    <div class="card-tier">Premium Member Card</div>
  </section>

  <section class="card card--back" aria-label="Kartenrückseite">
    <p class="holder-name">Loredane<br>Musterlady</p>
    <p class="holder-data holder-data--number">Kundennr.: xxxxxxxxxxxxxx</p>
    <p class="holder-data holder-data--code">CODE: XAIAG MAEIG</p>
    <p class="holder-data holder-data--security">Sicherheitscode: xxxxxxxxxx</p>
    <div class="holder-photo" role="img" aria-label="Porträtfoto der Karteninhaberin"></div>
    <p class="valid-until">Gültig bis: xx 20xx</p>
    <div class="brand-name">Amara-Lumi</div>
    <div class="nfc-field"></div>
  </section>
</main>
</body>
</html>
```